Business card for Eyelash extension salon in Beverly Hills,California USA

We need new business card for our salon in Beverly Hills. The salon name is 'Lashvera' . We would like to have...Business name: Lashvera Name of person: will provide later Address 4720 N.Alder Crest Ave Beverly Hills , CA 90210 Phone: will provide later (Text only) Web: www.lashverastudio.example Snapgrid icon, Circlebook icon follow us for seasonal campaign and news @lashverastudiolounge Design should look elegant, high-end, clean, simple, cohesive with my brand. Please refer my brand board. Business name color will be metallic bronzy color. Im thinking grey background or white background. Thanks

Target Market(s)

25-35. Gender neutral. People who are in Entertainment business industry.
This is High-end Eyelash extension salon in Beverly Hills

Industry/Entity Type

Beauty Salon

Contact Information for Business Card

Business name: Lashvera
Name of person: will provide later
Address 4720 N.Alder Crest Ave Beverly Hills , CA 90210
Phone: will provide later (Text only)
Web: www.lashverastudio.example
Snapgrid icon, Circlebook icon
follow us for seasonal campaign and news @lashverastudiolounge

Requirements
Must have
• Beautiful, elegant, clean and simple look but very attractive and modern
Should not have
• We don't like too clutter, too busy designs.

```html
<!DOCTYPE html>
<html lang="en">
<head>
<meta charset="utf-8">
<title>Lashvera Business Card</title>
<link rel="stylesheet" href="https://fonts.googleapis.com/css2?family=Libre+Bodoni:wght@400;500&family=Poppins:wght@300;400&display=swap">
<style>
  :root {
    --backdrop: #d6d6d6;
    --card-white: #ffffff;
    --panel-grey: #e8e8eb;
    --art-light: #ececef;
    --art-mid: #d7d7db;
    --ink: #3c3c3e;
    --bronze: #8a664f;
  }
  * { margin: 0; padding: 0; box-sizing: border-box; }
  html, body {
    width: 1200px;
    height: 965px;
    overflow: hidden;
    background: var(--backdrop);
  }
  .card {
    position: absolute;
    top: 159px;
    width: 382px;
    height: 669px;
    background: var(--card-white);
    overflow: hidden;
  }
  .card--front { left: 186px; }
  .card--back { left: 654px; }
  .card__bands {
    position: absolute;
    inset: 0;
    width: 382px;
    height: 669px;
  }
  .card__bands .band-grey { fill: var(--panel-grey); }
  .card__art {
    position: absolute;
    left: 8px;
    top: 8px;
    width: 366px;
    height: 232px;
    border-radius: 40px;
    background: radial-gradient(ellipse at 50% 70%, var(--art-mid) 0%, var(--art-light) 55%, var(--panel-grey) 100%);
  }
  .holder {
    position: absolute;
    left: 26px;
    top: 325px;
    color: var(--ink);
  }
  .holder__name {
    font-family: "Libre Bodoni", serif;
    font-weight: 500;
    font-size: 35px;
    letter-spacing: -0.5px;
    line-height: 1.1;
  }
  .holder__title {
    font-family: "Poppins", sans-serif;
    font-size: 13px;
    letter-spacing: 0.6px;
    margin-top: 6px;
  }
  .contact {
    position: absolute;
    left: 26px;
    top: 508px;
    font-family: "Poppins", sans-serif;
    font-size: 13px;
    letter-spacing: 0.6px;
    color: var(--ink);
    line-height: 24px;
  }
  .contact__address { padding-left: 108px; margin-bottom: 17px; }
  .contact__row { display: flex; }
  .contact__label { width: 75px; }
  .contact__colon { width: 33px; }
  .brand {
    position: absolute;
    left: 0;
    width: 382px;
    top: 478px;
    text-align: center;
    font-family: "Poppins", sans-serif;
    font-weight: 300;
    font-size: 42px;
    letter-spacing: 2px;
    color: var(--bronze);
  }
</style>
</head>
<body>

<section class="card card--front" aria-label="Business card front">
  <svg class="card__bands" viewBox="0 0 382 669" aria-hidden="true">
    <polygon class="band-grey" points="0,0 382,0 382,369 0,504"/>
  </svg>
  <div class="card__art" role="img" aria-label="Soft grey illustration of an eyebrow and a closed eye with long lashes"></div>
  <div class="holder">
    <h1 class="holder__name">Dana R. Whitford</h1>
    <p class="holder__title">DIRECTOR</p>
  </div>
  <div class="contact">
    <p class="contact__address">4720 N.ALDER CREST<br>AVE BEVERLY HILLS , CA 90210</p>
    <p class="contact__row"><span class="contact__label">PHONE</span><span class="contact__colon">:</span><span>310.555.0142</span></p>
    <p class="contact__row"><span class="contact__label">EMAIL</span><span class="contact__colon">:</span><span>HELLO@LASHVERA.EXAMPLE</span></p>
    <p class="contact__row"><span class="contact__label">WEB</span><span class="contact__colon">:</span><span>WWW.LASHVERASTUDIO.EXAMPLE</span></p>
  </div>
</section>

<section class="card card--back" aria-label="Business card back">
  <svg class="card__bands" viewBox="0 0 382 669" aria-hidden="true">
    <polygon class="band-grey" points="0,0 382,0 382,202 0,337"/>
  </svg>
  <div class="card__art" role="img" aria-label="Soft grey illustration of an eyebrow and a closed eye with long lashes"></div>
  <p class="brand">Lashvera</p>
</section>

</body>
</html>
```